Foot and ankle surgeon requires a website design

I need a website where prospective and established patients can obtain information and then direct them to making appointments. My practice is a highly professional surgical practice specialising in surgery to the foot and ankle. My title is Mr Colin Brasket, Podiatric Foot & Ankle Surgeon. My qualifications are: BSc MSc FACPS
The practice website will require information on: Locations, phone numbers to make appointments, general background on podiatric surgery,
I would like to include information on: my hospital appointments, surgical fellowships held, training programs undertaken, association memberships, publications written, links to useful websites
A page dedicated to common foot conditions would be useful and also a page with referral information including an online registration section that will be sent direct to the receptionist.
Examples of similar websites include:
http://www.dorvelquintaro.com.au/
http://www.haldenfootsurgeon.com.au/
I will provide files on logo, self photos and my personal training history etc.
Also if there is going to be a background theme I personally am associated with surfing and beach activities, it would be great if this was able to be reflected in the design.
Thank you.

```html
<!DOCTYPE html>
<html lang="en">
<head>
<meta charset="utf-8">
<title>Mr Colin Brasket – Podiatric Foot &amp; Ankle Surgeon</title>
<link href="https://fonts.googleapis.com/css2?family=Open+Sans:wght@400;600;700&family=PT+Serif:wght@400;700&display=swap" rel="stylesheet">
<style>
:root{
  --blue:#1f5aa6;
  --navy:#1b3f73;
  --orange:#f07a1a;
  --red:#d62c1f;
  --sky:#dcecf7;
  --sea:#9fc7e3;
  --sand:#e9dccb;
  --peach:#fde4d0;
  --grey:#ececec;
  --text:#555;
  --line:#d9d9d9;
}
*{margin:0;padding:0;box-sizing:border-box}
html,body{width:752px;height:1200px;overflow:hidden;background:#fff}
body{font-family:"Open Sans",Arial,sans-serif;color:var(--text);font-size:11px}
.page{position:relative;width:752px;height:1200px;overflow:hidden}

.site-header{position:absolute;left:0;top:0;width:752px;height:100px}
.brand{position:absolute;left:40px;top:24px;display:flex;align-items:center;gap:10px}
.brand-mark{width:34px;height:34px;border-radius:50%;background:var(--blue)}
.brand-name{font-family:"PT Serif",Georgia,serif;font-weight:700;font-size:22px;color:var(--blue);line-height:1}
.brand-tag{font-size:10px;color:var(--orange);margin-top:4px;font-weight:600}
.booking{position:absolute;right:40px;top:26px;text-align:left}
.booking-title{font-family:"PT Serif",Georgia,serif;font-size:17px;color:var(--orange)}
.booking-phone{display:flex;align-items:center;gap:6px;font-size:18px;font-weight:700;color:var(--red);margin-top:4px}

.main-nav{position:absolute;left:40px;top:100px;width:672px;height:20px;background:var(--blue);display:flex;align-items:center;padding-left:6px}
.main-nav a{color:#fff;text-decoration:none;font-size:11px;padding:0 13px;line-height:20px}
.main-nav a.active{background:var(--navy)}

.hero{position:absolute;left:40px;top:120px;width:672px;height:215px;background:linear-gradient(180deg,#eef6fc 0%,var(--sky) 55%,var(--sea) 75%,var(--sand) 100%)}
.hero-photo{position:absolute;right:0;top:0;width:340px;height:215px;background:radial-gradient(ellipse at 55% 55%,#e6c3a8 0%,#cfe2f0 45%,transparent 70%)}
.hero-copy{position:absolute;left:22px;top:40px;width:320px}
.hero-name{font-family:"PT Serif",Georgia,serif;font-size:26px;font-weight:700;color:var(--navy)}
.hero-role{font-family:"PT Serif",Georgia,serif;font-size:19px;color:var(--orange);margin-top:2px}
.hero-spec{font-family:"PT Serif",Georgia,serif;font-size:14px;color:var(--navy);margin-top:2px}
.hero-text{font-size:9px;line-height:1.5;margin-top:10px;color:#4f6a86}
.btn-more{display:inline-block;background:var(--blue);color:#fff;font-size:9px;padding:4px 10px;border-radius:3px;margin-top:10px}

.conditions{position:absolute;left:40px;top:350px;width:672px;height:280px}
.section-title{display:flex;align-items:center;justify-content:center;gap:14px;font-size:17px;color:#444;letter-spacing:.5px}
.section-title::before,.section-title::after{content:"";width:170px;border-top:1px solid var(--line)}
.section-title em{font-style:normal;color:var(--red)}
.condition-list{display:flex;justify-content:space-between;width:560px;margin:48px auto 0}
.condition{width:120px;text-align:center;font-size:11px;color:#333}
.condition-img{width:110px;height:110px;border-radius:50%;margin:0 auto 10px;background:radial-gradient(circle at 50% 55%,#e85a4a 0%,#c9a99a 35%,#8b8b8b 70%,#5a5a5a 100%);border:3px solid #fff;box-shadow:0 0 0 1px var(--line)}
.arrow{position:absolute;top:120px}
.arrow.left{left:-6px}.arrow.right{right:-6px}

.panels{position:absolute;left:40px;top:637px;width:672px;height:230px;display:flex;gap:6px}
.panel{flex:1;background:#f6f6f6;padding:10px 12px;position:relative}
.panel-head{display:flex;align-items:center;gap:6px;font-family:"PT Serif",Georgia,serif;font-size:14px;color:#333;margin-bottom:8px}
.panel-head em{font-style:normal;color:var(--orange)}
.panel.booking-form{background:var(--peach)}
.field{height:18px;background:#fff;border:1px solid #f1c9a9;font-size:9px;color:#aaa;padding-left:6px;line-height:16px;margin-bottom:6px}
.field-label{font-size:9px;color:#555;margin:4px 0 3px}
.field-row{display:flex;gap:6px}
.field-row .field{width:60px}
.btn-booking{display:flex;align-items:center;justify-content:space-between;background:var(--orange);color:#fff;font-weight:700;font-size:12px;padding:5px 10px;margin-top:10px;width:180px}
.panel-text{font-size:8px;line-height:1.45;color:#555}
.panel-photo{height:92px;margin-top:8px;background:linear-gradient(135deg,#c9dcea,#6f95b5 60%,#3f5f7f)}
.faces{display:flex;gap:5px;margin-top:8px}
.face{flex:1;height:92px;background:linear-gradient(180deg,#e7cdb8,#b08a70)}
.panel-link{font-size:8px;color:var(--blue);margin-top:6px}

.site-footer{position:absolute;left:40px;top:910px;width:672px;height:135px;background:var(--grey);display:flex;padding:14px 20px;gap:20px}
.foot-col{flex:1}
.foot-col h4{font-size:11px;color:#333;font-weight:600;margin-bottom:6px}
.foot-col p,.foot-col li{font-size:9px;line-height:1.5;list-style:none;color:#555}
.map{height:82px;background:linear-gradient(135deg,#e3e6da,#cfd8c4)}

.bottom-brand{position:absolute;left:0;top:1070px;width:752px;text-align:center}
.bottom-brand .brand-line{display:inline-flex;align-items:center;gap:8px}
.bottom-brand .brand-mark{width:26px;height:26px}
.bottom-brand .brand-name{font-size:18px}
.copyright{font-size:9px;color:#777;margin-top:16px}
</style>
</head>
<body>
<div class="page">

  <header class="site-header">
    <div class="brand">
      <span class="brand-mark"></span>
      <div>
        <div class="brand-name">Mr Colin Brasket</div>
        <div class="brand-tag">Podiatric Foot &amp; Ankle Surgeon</div>
      </div>
    </div>
    <div class="booking">
      <div class="booking-title">Book An Online Appointment</div>
      <div class="booking-phone">
        <svg width="18" height="18" viewBox="0 0 24 24"><path fill="#d62c1f" d="M6.6 10.8a15.1 15.1 0 0 0 6.6 6.6l2.2-2.2c.3-.3.7-.4 1-.2 1.1.4 2.3.6 3.6.6.6 0 1 .4 1 1V20c0 .6-.4 1-1 1A17 17 0 0 1 3 4c0-.6.4-1 1-1h3.5c.6 0 1 .4 1 1 0 1.3.2 2.5.6 3.6.1.3 0 .7-.2 1z"/></svg>
        Call Now !! 08 9730 2186
      </div>
    </div>
  </header>

  <nav class="main-nav">
    <a class="active">Home</a><a>About</a><a>Patients</a><a>Podiatric Surgery</a><a>Appointments</a><a>Blog</a><a>FAQ</a><a>Contact Us</a>
  </nav>

  <section class="hero">
    <div class="hero-photo" role="img" aria-label="Bare feet walking on a sandy beach at the water's edge"></div>
    <div class="hero-copy">
      <div class="hero-name">Mr.Colin Brasket</div>
      <div class="hero-role">Podiatric Foot &amp; Ankle Surgeon</div>
      <div class="hero-spec">(specialising in surgery to the foot and ankle)</div>
      <p class="hero-text">Lorem ipsum dolor sit amet, consectetur adipiscing elit, sed diam nonummy nibh euismod tincidunt ut laoreet dolore magna aliquam erat volutpat.</p>
      <span class="btn-more">Read More</span>
    </div>
  </section>

  <section class="conditions">
    <h2 class="section-title"><span>COMMON <em>FOOT CONDITIONS</em></span></h2>
    <svg class="arrow left" width="16" height="30" viewBox="0 0 16 30"><path d="M13 3 3 15l10 12" fill="none" stroke="#777" stroke-width="3"/></svg>
    <svg class="arrow right" width="16" height="30" viewBox="0 0 16 30"><path d="M3 3l10 12L3 27" fill="none" stroke="#777" stroke-width="3"/></svg>
    <div class="condition-list">
      <div class="condition"><div class="condition-img" role="img" aria-label="Ankle replacement illustration"></div>Ankle Replacement</div>
      <div class="condition"><div class="condition-img" role="img" aria-label="Ankle trauma illustration"></div>Ankle Trauma</div>
      <div class="condition"><div class="condition-img" role="img" aria-label="Tendon rupture illustration"></div>Tendon Rupture</div>
      <div class="condition"><div class="condition-img" role="img" aria-label="Ankle pain illustration"></div>Ankle Pain</div>
    </div>
  </section>

  <section class="panels">
    <div class="panel booking-form">
      <div class="panel-head">
        <svg width="14" height="14" viewBox="0 0 14 14"><rect x="1" y="2" width="12" height="11" fill="none" stroke="#555"/><path d="M1 5h12" stroke="#555"/></svg>
        <span>My Hospital <em>Appointments</em></span>
      </div>
      <div class="field">Name</div>
      <div class="field">Contact Number</div>
      <div class="field-label">Preferred Date?</div>
      <div class="field-row"><div class="field">dd</div><div class="field">mm</div></div>
      <div class="field-label">Preferred Time?</div>
      <div class="field-row"><div class="field">hh</div><div class="field">mm</div></div>
      <div class="btn-booking">Request Booking
        <svg width="14" height="14" viewBox="0 0 14 14"><rect width="14" height="14" rx="2" fill="#fff"/><path d="M3 7l3 3 5-6" fill="none" stroke="#f07a1a" stroke-width="2"/></svg>
      </div>
    </div>
    <div class="panel">
      <div class="panel-head">
        <svg width="14" height="14" viewBox="0 0 14 14"><circle cx="7" cy="7" r="6" fill="none" stroke="#555"/></svg>
        <span>Surgical Fellowship held</span>
      </div>
      <p class="panel-text">Lorem ipsum dolor sit amet, consectetur adipiscing elit, sed diam nonummy nibh euismod tincidunt ut laoreet dolore magna.</p>
      <div class="panel-photo" role="img" aria-label="Surgical team at work in an operating theatre"></div>
      <div class="panel-link">Read More »</div>
    </div>
    <div class="panel">
      <div class="panel-head">
        <svg width="14" height="14" viewBox="0 0 14 14"><path d="M1 5l6-3 6 3-6 3z" fill="#555"/><path d="M4 7v3c2 1.5 4 1.5 6 0V7" fill="none" stroke="#555"/></svg>
        <span>Training Programs</span>
      </div>
      <p class="panel-text">Lorem ipsum dolor sit amet, consectetur adipiscing elit, sed diam nonummy nibh euismod tincidunt ut laoreet dolore magna.</p>
      <div class="faces">
        <div class="face" role="img" aria-label="Portrait of a trainee"></div>
        <div class="face" role="img" aria-label="Portrait of a trainee"></div>
        <div class="face" role="img" aria-label="Portrait of a trainee"></div>
      </div>
      <div class="panel-link">Read More »</div>
    </div>
  </section>

  <footer class="site-footer">
    <div class="foot-col">
      <h4>Menu Links</h4>
      <ul><li>About Us</li><li>Our Services</li><li>About Doctor</li><li>For Patients</li><li>Case Studies</li></ul>
    </div>
    <div class="foot-col">
      <h4>Support Links</h4>
      <ul><li>Terms and conditions</li><li>Legal Notice</li><li>Private Policy</li></ul>
    </div>
    <div class="foot-col">
      <h4>Contact Info</h4>
      <p>48 Tidewater Coastal<br>Road<br>PO Box 2207<br>Marrowby WA 6612<br>Phone 08 9730 2186<br>Fax 08 9730 2187</p>
    </div>
    <div class="foot-col">
      <h4>Find Us</h4>
      <div class="map" role="img" aria-label="Street map showing the practice location"></div>
    </div>
  </footer>

  <div class="bottom-brand">
    <div class="brand-line">
      <span class="brand-mark"></span>
      <span class="brand-name">Mr Colin Brasket</span>
    </div>
    <div class="brand-tag">Podiatric Foot &amp; Ankle Surgeon</div>
    <p class="copyright">Copyright © 2014 Mr Colin Brasket. All rights reserved.</p>
  </div>

</div>
</body>
</html>
```